real esate business card with company logo and name

we need a business card design for a real esate company

The company name is Walsh & Brand Pty Ltd, and we have our logo designed and will upload. We want classic or moden feel. Black or white background. looks more textured. Should include folowinginformations
Owen Walsh and Lucy Brand
Sales Agents & Onsite Manager
p: 07 5948 2063
F: 07 5948 2174
M:0431 857 219
3/42 Marlow Crescent, FERNLEA QLD 4213

We want this business card looks professonal. Thank you in advance.

Industry/Entity Type

Real Estate Agent

Contact Information for Business Card

Owen Walsh and Lucy Brand
Onsite Manager & Sales Agents
p: 07 5948 2063
M:0431 857 219

Font styles to use
Serif

Colors
000000
fbfbfb
333333
959595

Requirements
Must have
• company logo and name, black or white back ground

```html
<!DOCTYPE html>
<html lang="en">
<head>
<meta charset="utf-8">
<title>Walsh &amp; Brand Pty Ltd — Business Card</title>
<link href="https://fonts.googleapis.com/css2?family=Lato:wght@400;700&display=swap" rel="stylesheet">
<style>
  :root {
    --ink: #000000;
    --paper: #fbfbfb;
    --charcoal: #333333;
    --steel: #959595;
    --backdrop: #2e2e2e;
  }
  html, body {
    margin: 0;
    padding: 0;
    width: 1200px;
    height: 1086px;
    overflow: hidden;
    background: var(--backdrop);
    font-family: "Lato", Arial, sans-serif;
  }
  .card {
    position: absolute;
    left: 254px;
    width: 677px;
    height: 386px;
    box-sizing: border-box;
  }
  .card--front { top: 126px; background: var(--paper); color: var(--ink); }
  .card--back  { top: 586px; background: var(--ink); }

  .company {
    position: absolute;
    display: flex;
    align-items: center;
    gap: 12px;
    color: var(--steel);
    font-weight: 400;
    letter-spacing: 0.06em;
    text-transform: uppercase;
    white-space: nowrap;
  }
  .company__square {
    background: var(--steel);
    flex: none;
  }
  .card--front .company { right: 34px; top: 176px; font-size: 14px; }
  .card--front .company__square { width: 12px; height: 12px; }
  .card--back .company {
    left: 0; right: 0; top: 244px;
    justify-content: center;
    font-size: 20px;
  }
  .card--back .company__square { width: 18px; height: 18px; }

  .agent__name {
    position: absolute;
    left: 32px; top: 189px;
    margin: 0;
    font-size: 27px;
    font-weight: 700;
    line-height: 1;
  }
  .agent__role {
    position: absolute;
    left: 32px; top: 223px;
    margin: 0;
    font-size: 20px;
    font-weight: 400;
    line-height: 1;
    color: var(--charcoal);
  }
  .rule {
    position: absolute;
    left: 161px; top: 237px;
    width: 485px; height: 1px;
    background: var(--ink);
  }

  .contacts {
    position: absolute;
    left: 32px; top: 290px;
    margin: 0; padding: 0;
    list-style: none;
    font-size: 19px;
    line-height: 23.5px;
  }
  .contacts li { display: flex; align-items: center; gap: 6px; }
  .contacts svg { width: 16px; height: 16px; flex: none; }

  .address {
    position: absolute;
    right: 31px; top: 315px;
    margin: 0;
    font-style: normal;
    font-size: 17.5px;
    line-height: 22px;
    text-align: right;
  }

  .band {
    position: absolute;
    left: 0; bottom: 0;
    width: 100%; height: 12px;
    display: flex;
  }
  .band__dark { width: 536px; background: var(--ink); }
  .band__light { flex: 1; background: #5f5f5f; }
</style>
</head>
<body>

<section class="card card--front" aria-label="Business card front">
  <div class="company"><span class="company__square"></span>Walsh &amp; Brand Pty Ltd</div>

  <h1 class="agent__name">Owen Walsh</h1>
  <p class="agent__role">Sales Agents</p>
  <div class="rule"></div>

  <ul class="contacts">
    <li>
      <svg viewBox="0 0 16 16" aria-label="Mobile"><rect x="4" y="1" width="8" height="14" rx="1.5" fill="none" stroke="#000" stroke-width="1.5"/><rect x="7" y="12" width="2" height="1.2" fill="#000"/></svg>
      0431 857 219
    </li>
    <li>
      <svg viewBox="0 0 16 16" aria-label="Phone"><path d="M1 6 Q8 1 15 6 L13 8 L11 6.5 V5.5 Q8 4.5 5 5.5 V6.5 L3 8 Z" fill="#000"/><rect x="3" y="8.5" width="10" height="6" rx="1" fill="#000"/></svg>
      07 5948 2063
    </li>
    <li>
      <svg viewBox="0 0 16 16" aria-label="Fax"><rect x="4" y="1" width="8" height="4" fill="#000"/><rect x="1" y="5.5" width="14" height="6" rx="1" fill="#000"/><rect x="4" y="10" width="8" height="5" fill="#fff" stroke="#000" stroke-width="1.2"/></svg>
      07 5948 2174
    </li>
  </ul>

  <address class="address">3/42 Marlow Crescent<br>FERNLEA QLD 4213</address>

  <div class="band"><span class="band__dark"></span><span class="band__light"></span></div>
</section>

<section class="card card--back" aria-label="Business card back">
  <div class="company"><span class="company__square"></span>Walsh &amp; Brand Pty Ltd</div>
</section>

</body>
</html>
```